hotel's Website

Hotels website redesign for reference pictures, logo etc see http://restwellharbour.co.uk/

1. 2-3 Special offers on the main page.
2. Booking calender
3. Location Map
4. Picture gallery.
5. Journeymarks reviews.
6. short description
7. Social Media sharing.
8 Phone number and address.

Industry/Entity Type

Hotel

Requirements
Must have
• 1. 2-3 Special offers on the main page.
2. Booking calender
3. Location Map
4. Picture gallery.
5. Journeymarks reviews.
6. short description
7. Social Media sharing.

```html
<!DOCTYPE html>
<html lang="en">
<head>
<meta charset="utf-8">
<title>Restwell Harbour – Hotel</title>
<link rel="stylesheet" href="https://fonts.googleapis.com/css2?family=Bitter:wght@400;700&family=Roboto:wght@400;500;700&family=Oswald:wght@400;500&display=swap">
<style>
:root{
  --wood-dark:#1a0b05;
  --wood:#5a2a14;
  --wood-light:#8a4a28;
  --blue:#1767bd;
  --blue-dark:#0f4f98;
  --red:#e3162b;
  --orange:#f26a1b;
  --text:#555;
  --heading:#333;
  --yellow:#ffe400;
  --white:#fff;
}
*{box-sizing:border-box;margin:0;padding:0}
html,body{width:1089px;height:1200px;overflow:hidden;background:var(--wood-dark)}
.canvas{position:relative;width:1089px;height:1200px;overflow:hidden}
.page{position:absolute;left:0;top:0;width:1280px;height:1410px;overflow:hidden;transform:scale(.8508);transform-origin:0 0;
  font-family:'Bitter',serif;color:var(--text);
  background:
    radial-gradient(ellipse 120px 60px at 130px 10px,rgba(255,240,220,.55),transparent),
    radial-gradient(ellipse 120px 60px at 1180px 10px,rgba(255,240,220,.55),transparent),
    radial-gradient(ellipse 140px 60px at 540px 0,rgba(255,240,220,.4),transparent),
    linear-gradient(90deg,rgba(0,0,0,.15) 0 2px,transparent 2px 90px),
    linear-gradient(180deg,var(--wood-light) 0,var(--wood) 260px,#2a1208 520px,#000 720px,#000);
  background-size:auto,auto,auto,90px 100%,auto}
.abs{position:absolute}
.translate{left:944px;top:15px;font:500 12px 'Roboto',sans-serif;color:#fff}
.lang{left:1020px;top:8px;width:120px;height:28px;background:linear-gradient(#fff,#ddd);border:1px solid #bbb;border-radius:2px;font:13px 'Roboto',sans-serif;color:#333;padding:6px 0 0 8px}
.lang .flag{display:inline-block;width:22px;height:14px;background:#2a4fa0;vertical-align:-2px;margin-right:8px}
.lang .caret{position:absolute;right:8px;top:11px;border:6px solid transparent;border-top-color:#444}
.top-phone{left:960px;top:40px;font:500 16px 'Roboto',sans-serif;color:#fff;display:flex;align-items:center;gap:6px;white-space:nowrap}
.top-mail{left:905px;top:66px;font:500 12px 'Roboto',sans-serif;color:#fff;display:flex;align-items:center;gap:6px;white-space:nowrap}
.sheet{left:141px;top:87px;width:1000px;height:1323px;background:var(--white);border-radius:10px 10px 0 0}
.logo-arch{left:553px;top:37px;width:178px;height:120px;background:var(--white);border-radius:90px 90px 0 0}
.logo{left:580px;top:50px;width:125px;height:137px;background:var(--white);text-align:center;z-index:3;box-shadow:0 2px 4px rgba(0,0,0,.15)}
.logo .place{font:700 8px 'Bitter',serif;color:var(--blue);letter-spacing:.5px;margin-top:5px}
.logo .mark{width:50px;height:50px;background:var(--blue);margin:6px auto 6px}
.logo .name{font:700 15px/16px 'Bitter',serif;color:var(--blue)}
.logo .by{font:8px 'Bitter',serif;color:#222;margin-top:8px}
.nav{left:160px;top:113px;width:960px;height:50px;background:linear-gradient(var(--blue),var(--blue-dark))}
.nav .home{width:57px;height:50px;background:linear-gradient(var(--orange),var(--red));display:flex;align-items:center;justify-content:center}
.nav a{font:12.5px 'Bitter',serif;color:#fff;text-decoration:none;letter-spacing:.6px;position:absolute;top:17px;white-space:nowrap}
.slider{left:160px;top:163px;width:960px;height:439px;border-radius:0 0 10px 10px;overflow:hidden;
  background:linear-gradient(180deg,#3b2e5a 0,#8b5a6a 35%,#c97a3f 58%,#3a1f3a 72%,#6a2a7a 86%,#1b1020)}
.slide-arrow{top:180px}
.thumb{top:360px;height:68px;width:114px;border:2px solid var(--yellow);border-radius:6px}
.thumb.active{top:338px;height:86px;width:152px}
.sec-title{font:400 19px 'Bitter',serif;color:var(--heading);display:flex;align-items:center;gap:9px;border-bottom:1px dotted #bbb;width:573px;padding-bottom:6px;white-space:nowrap}
.dot{width:19px;height:19px;border-radius:50%;background:linear-gradient(var(--yellow),var(--orange) 55%,var(--red))}
.intro{left:196px;top:688px;width:572px;font:12.5px/18px 'Bitter',serif;letter-spacing:.35px}
.read-more{left:687px;top:796px;font:11.5px 'Bitter',serif;color:#222;display:flex;align-items:center;gap:5px;white-space:nowrap}
.go{width:17px;height:17px;border-radius:50%;background:#111;display:flex;align-items:center;justify-content:center}
.offers{left:198px;top:892px;width:561px;height:232px;border:1px solid #e4e4e4;background:linear-gradient(#f4f4f4,#fff 40%,#fff)}
.offer{top:908px;width:220px;height:198px;border:5px solid var(--yellow);background:#fff;padding:5px}
.offer .pic{width:100%;height:100%;position:relative}
.offer .tag{position:absolute;right:0;bottom:0;background:rgba(255,255,255,.7);padding:6px 8px;font-family:'Oswald',sans-serif;text-align:center;line-height:1}
.side-arrow{top:990px;width:22px;height:48px;background:#222;display:flex;align-items:center;justify-content:center}
.newsletter{left:193px;top:1144px;width:491px;height:35px;display:flex;border:1px solid #ccc}
.newsletter .label{width:123px;background:linear-gradient(#555,#222);color:#fff;font:700 12.5px 'Bitter',serif;letter-spacing:.6px;display:flex;align-items:center;justify-content:center}
.newsletter .field{flex:1;background:linear-gradient(#fff,#eee);font:13px 'Bitter',serif;color:#999;padding:9px 13px}
.subscribe{left:690px;top:1144px;width:78px;height:35px;background:#ef3c55;color:#fff;font:14px 'Bitter',serif;display:flex;align-items:center;justify-content:center}
.ribbon{left:814px;width:279px;height:47px;background:linear-gradient(var(--red),var(--orange) 60%,#ffb000);color:#fff;font:700 15px 'Bitter',serif;padding:10px 22px;border-radius:3px 3px 0 0;white-space:nowrap}
.card{left:823px;width:260px;background:#fff;border-radius:0 0 8px 8px;box-shadow:0 3px 5px rgba(0,0,0,.2)}
.month{left:834px;top:692px;font:400 19px 'Oswald',sans-serif;color:#555}
.next{left:1058px;top:694px;width:16px;height:16px;border-radius:50%;background:#eee;border:1px solid #ccc;display:flex;align-items:center;justify-content:center}
.cal{left:830px;top:721px;width:246px;border-collapse:collapse;font:12px 'Roboto',sans-serif;color:#444;text-align:center}
.cal th{background:#a8a8a8;color:#fff;font-weight:700;font-size:10.5px;height:26px}
.cal td{border:1px solid #ddd;height:26.5px}
.cal td.today{color:var(--red);font-weight:700}
.book{left:985px;top:883px;width:82px;height:23px;background:linear-gradient(#ffe84a,#e8c400);border:1px solid #c9a800;border-radius:3px;font:11px 'Bitter',serif;color:#333;display:flex;align-items:center;justify-content:center;white-space:nowrap}
.review{left:873px;top:992px;width:184px;font:12px/18px 'Bitter',serif;color:#555;letter-spacing:.5px}
.quote{font:700 50px/1 'Bitter',serif;color:#ccc}
.review-more{left:997px;top:1096px;font:italic 700 11px 'Bitter',serif;color:#444}
.follow{left:822px;top:1152px;font:16px 'Bitter',serif;color:#333}
.social{top:1146px;width:32px;height:32px;border-radius:5px}
.footer-rule{left:193px;top:1214px;width:900px;height:1px;background:#e5e5e5}
.f-title{top:1240px;font:700 18px 'Roboto',sans-serif;color:var(--red)}
.f-split{top:1245px;width:1px;height:150px;background:linear-gradient(#fff,var(--red) 30%,var(--red) 70%,#fff)}
.qlink{font:13px 'Bitter',serif;color:#444;display:flex;align-items:center;gap:10px;white-space:nowrap}
.partners{left:480px;top:1274px;width:205px;font:10.5px/12px 'Roboto',sans-serif;color:#444}
.partners p{margin-bottom:7px}
.partners li{list-style:none;font:10.5px/12px 'Bitter',serif;color:#222;white-space:nowrap}
.map{left:718px;top:1276px;width:145px;height:116px;background:linear-gradient(135deg,#dfe8d0,#c8dcb4 50%,#e9e3d3)}
.contact{left:888px;font:12.5px/18px 'Roboto',sans-serif;color:#444;display:flex;gap:12px;align-items:flex-start;white-space:nowrap}
.contact svg{flex:none;margin-top:2px}
</style>
</head>
<body>
<div class="canvas">
<div class="page">

  <header>
    <div class="abs translate">Translate to :</div>
    <div class="abs lang"><span class="flag"></span>English<span class="caret"></span></div>
    <div class="abs top-phone">
      <svg width="22" height="22" viewBox="0 0 22 22"><circle cx="11" cy="11" r="10" fill="none" stroke="#fff" stroke-width="1.6"/><path d="M7.5 6.5c1-.5 1.5 0 2 1.2l.3 1c.1.5-.5.9-.7 1.2.6 1.3 1.5 2.3 2.8 2.9.3-.3.7-.9 1.2-.7l1 .4c1.1.5 1.6 1 1.1 2-1 1.6-3 1.3-5.2-.6-2.4-2.2-3.4-4.6-2.5-6.4z" fill="#fff"/></svg>
      + 44 (0) 20 5550 1842
    </div>
    <div class="abs top-mail">
      <svg width="18" height="12" viewBox="0 0 18 12"><rect x="1" y="1" width="16" height="10" fill="none" stroke="#fff" stroke-width="1.6"/><path d="M1 1l8 6 8-6" fill="none" stroke="#fff" stroke-width="1.6"/></svg>
      STAY@RESTWELLHARBOUR.CO.UK
    </div>
  </header>

  <div class="abs sheet"></div>
  <div class="abs logo-arch"></div>

  <nav class="abs nav">
    <div class="home">
      <svg width="24" height="20" viewBox="0 0 24 20"><path d="M12 1L1 10h3v9h6v-6h4v6h6v-9h3z" fill="#4a1d0a"/></svg>
    </div>
    <a style="left:76px">OUR ROOMS</a>
    <a style="left:180px">ATTRACTIONS</a>
    <a style="left:295px">LONDON EVENTS</a>
    <a style="left:565px">SPECIAL OFFERS</a>
    <a style="left:694px">PHOTOS</a>
    <a style="left:775px">DIRECTIONS</a>
    <a style="left:881px">CONTACT</a>
  </nav>

  <div class="abs logo">
    <div class="place">HARBOUR - QUAYSIDE</div>
    <div class="mark"></div>
    <div class="name">Restwell<br>Harbour</div>
    <div class="by">BY HARBOURLINE HOTELS</div>
  </div>

  <section class="abs slider" role="img" aria-label="Night view of the city riverside with an illuminated observation wheel and bridge">
    <svg class="abs slide-arrow" style="left:34px" width="26" height="36" viewBox="0 0 26 36"><path d="M20 3L6 18l14 15" fill="none" stroke="#ffdd00" stroke-width="6"/></svg>
    <svg class="abs slide-arrow" style="left:898px" width="26" height="36" viewBox="0 0 26 36"><path d="M6 3l14 15L6 33" fill="none" stroke="#ffdd00" stroke-width="6"/></svg>
    <div class="abs thumb" style="left:33px;background:linear-gradient(#eee,#c8a080 50%,#b8202a)" role="img" aria-label="Double bedroom"></div>
    <div class="abs thumb" style="left:157px;background:linear-gradient(#bbb,#555 50%,#888)" role="img" aria-label="Breakfast drinks station"></div>
    <div class="abs thumb" style="left:280px;background:linear-gradient(#e8e2d8,#b07a4a 60%,#ddd)" role="img" aria-label="Hotel corridor"></div>
    <div class="abs thumb active" style="left:404px;background:linear-gradient(#3b2e5a,#c97a3f 55%,#6a2a7a)" role="img" aria-label="Riverside at night"></div>
    <div class="abs thumb" style="left:565px;background:linear-gradient(#f0e8dc,#b06a38 60%,#8a4a28)" role="img" aria-label="Breakfast room"></div>
    <div class="abs thumb" style="left:690px;background:linear-gradient(#eef1f3,#d8dde2)" role="img" aria-label="Bathroom"></div>
    <div class="abs thumb" style="left:814px;background:linear-gradient(#f2ead8,#c4a070 50%,#3a50a0)" role="img" aria-label="Twin bedroom"></div>
  </section>

  <main>
    <h2 class="abs sec-title" style="left:194px;top:650px"><span class="dot"></span>Welcome To Restwell Harbour</h2>
    <p class="abs intro">Lorem ipsum dolor sit amet, consectetuer adipiscing elit, sed diam nonummy nibh euismod tincidunt ut laoreet dolore magna aliquam erat volutpat. Ut wisi enim ad minim veniam, quis nostrud exerci tation ullamcorper suscipit lobortis nisl ut aliquip. Lorem ipsum dolor sit amet, consectetuer adipiscing elit, sed diam nonummy nibh euismod tincidunt ut laoreet dolore magna aliquam erat volutpat. Ut wisi enim ad minim veniam, quis nostrud exerci tation ullamcorper suscipit lobortis nisl ut aliquip.</p>
    <div class="abs read-more"><span class="go"><svg width="8" height="8" viewBox="0 0 8 8"><path d="M2 1l4 3-4 3" fill="none" stroke="#ffdd00" stroke-width="2"/></svg></span>Read more</div>

    <h2 class="abs sec-title" style="left:194px;top:850px"><span class="dot"></span>Our Special Offers</h2>
    <div class="abs offers"></div>
    <div class="abs side-arrow" style="left:194px;border-radius:0 24px 24px 0"><svg width="12" height="14" viewBox="0 0 12 14"><path d="M9 1L3 7l6 6" fill="none" stroke="#ffdd00" stroke-width="3"/></svg></div>
    <div class="abs side-arrow" style="left:741px;border-radius:24px 0 0 24px"><svg width="12" height="14" viewBox="0 0 12 14"><path d="M3 1l6 6-6 6" fill="none" stroke="#fff" stroke-width="3"/></svg></div>

    <article class="abs offer" style="left:235px">
      <div class="pic" style="background:linear-gradient(150deg,#d9b39a,#8a6a5a 50%,#3a2a24)" role="img" aria-label="Spa foot treatment">
        <div class="tag"><div style="color:var(--red);font-size:32px;font-weight:500">SPA</div><div style="color:#222;font-size:20px">TREATMENT</div><div style="font-size:20px;color:#222;font-weight:500">Save <span style="color:var(--red);font-size:34px">25%</span></div></div>
      </div>
    </article>
    <article class="abs offer" style="left:504px">
      <div class="pic" style="background:linear-gradient(150deg,#e8e4e0,#9a8a8a 50%,#4a3a40)" role="img" aria-label="Shopping for handbags in a boutique">
        <div class="tag"><div style="color:var(--red);font-size:26px;font-weight:500">Shopping</div><div style="color:#222;font-size:18px">IN</div><div style="color:var(--blue);font-size:34px;font-weight:500">LONDON</div></div>
      </div>
    </article>

    <form class="abs newsletter"><div class="label">NEWSLETTER</div><div class="field">E-mail address</div></form>
    <div class="abs subscribe">Subscribe</div>
  </main>

  <aside>
    <div class="abs card" style="top:680px;height:232px"></div>
    <div class="abs ribbon" style="top:643px">BOOKING CALENDAR</div>
    <div class="abs month">November 2013</div>
    <div class="abs next"><svg width="7" height="9" viewBox="0 0 7 9"><path d="M1 1l4 3.5L1 8" fill="none" stroke="#222" stroke-width="2"/></svg></div>
    <table class="abs cal">
      <tr><th>MON</th><th>TUE</th><th>WED</th><th>THU</th><th>FRI</th><th>SAT</th><th>SUN</th></tr>
      <tr><td>1</td><td>2</td><td>3</td><td>4</td><td>5</td><td>6</td><td>7</td></tr>
      <tr><td>8</td><td>9</td><td>10</td><td>11</td><td>12</td><td>13</td><td>14</td></tr>
      <tr><td>15</td><td>16</td><td>17</td><td>18</td><td>19</td><td>20</td><td class="today">21</td></tr>
      <tr><td>22</td><td>23</td><td>24</td><td>25</td><td>26</td><td>27</td><td>28</td></tr>
      <tr><td>29</td><td>30</td><td colspan="5"></td></tr>
    </table>
    <div class="abs book">Click To Book</div>

    <div class="abs card" style="top:975px;height:147px"></div>
    <div class="abs ribbon" style="top:938px;padding:0 16px 0 28px;display:flex;align-items:center;gap:7px;font-size:14px">
      <span style="width:12px;height:12px;border-radius:50%;background:#fff;display:inline-block;flex:none"></span>
      <span>Journeymarks REVIEWS</span>
      <svg style="margin-left:auto;flex:none" width="34" height="12" viewBox="0 0 36 12"><path d="M2 6h12M2 6l5-5M2 6l5 5M22 6h12M34 6l-5-5M34 6l-5 5" fill="none" stroke="#fff" stroke-width="2.5"/></svg>
    </div>
    <div class="abs quote" style="left:840px;top:982px">“</div>
    <p class="abs review">Lorem ipsum dolor sit amet, adipiscing elit. Mauris felis ante,semper et, accumsan quis diam.tincidunt felis nec magna feugiat ulla atvesti bulum.</p>
    <div class="abs quote" style="left:923px;top:1082px">”</div>
    <div class="abs review-more">Read More</div>

    <div class="abs follow">Follow Us</div>
    <div class="abs social" style="left:915px;background:#3b5ea8"></div>
    <div class="abs social" style="left:955px;background:#36a9e0"></div>
    <div class="abs social" style="left:995px;background:#1b6fae"></div>
    <div class="abs social" style="left:1035px;background:#f07b1e"></div>
  </aside>

  <footer>
    <div class="abs footer-rule"></div>

    <h3 class="abs f-title" style="left:195px">Quick Links</h3>
    <div class="abs" style="left:195px;top:1272px;display:grid;grid-template-columns:128px 120px;row-gap:17px">
      <div class="qlink"><svg width="14" height="10" viewBox="0 0 14 10"><path d="M0 3h8V0l6 5-6 5V7H0z" fill="#f5c400"/></svg>Home</div>
      <div class="qlink"><svg width="14" height="10" viewBox="0 0 14 10"><path d="M0 3h8V0l6 5-6 5V7H0z" fill="#f5c400"/></svg>Special Offers</div>
      <div class="qlink"><svg width="14" height="10" viewBox="0 0 14 10"><path d="M0 3h8V0l6 5-6 5V7H0z" fill="#f5c400"/></svg>Our Rooms</div>
      <div class="qlink"><svg width="14" height="10" viewBox="0 0 14 10"><path d="M0 3h8V0l6 5-6 5V7H0z" fill="#f5c400"/></svg>Photos</div>
      <div class="qlink"><svg width="14" height="10" viewBox="0 0 14 10"><path d="M0 3h8V0l6 5-6 5V7H0z" fill="#f5c400"/></svg>Attractions</div>
      <div class="qlink"><svg width="14" height="10" viewBox="0 0 14 10"><path d="M0 3h8V0l6 5-6 5V7H0z" fill="#f5c400"/></svg>Direction</div>
      <div class="qlink"><svg width="14" height="10" viewBox="0 0 14 10"><path d="M0 3h8V0l6 5-6 5V7H0z" fill="#f5c400"/></svg>London Events</div>
      <div class="qlink"><svg width="14" height="10" viewBox="0 0 14 10"><path d="M0 3h8V0l6 5-6 5V7H0z" fill="#f5c400"/></svg>Contact Us</div>
    </div>

    <div class="abs f-split" style="left:460px"></div>
    <h3 class="abs f-title" style="left:479px">Partner Hotels</h3>
    <div class="abs partners">
      <p>This hotel is owned and operated by the Northgate Hotel Group, please take a look of some of our other hotels below:</p>
      <ul>
        <li>Lockside Lodge - Camden Wharf</li>
        <li>Wayfarer Express - Earls Court</li>
        <li>Millhouse Central Hotel</li>
        <li>Brightstay Victoria</li>
        <li>Brightstay Paddington</li>
        <li>Restwell Suites - King's Cross</li>
      </ul>
    </div>

    <div class="abs f-split" style="left:698px"></div>
    <h3 class="abs f-title" style="left:718px">Contact Info</h3>
    <div class="abs map" role="img" aria-label="Street map showing the hotel location"></div>
    <div class="abs contact" style="top:1274px">
      <svg width="14" height="16" viewBox="0 0 14 16"><path d="M7 1a5 5 0 0 0-5 5c0 4 5 9 5 9s5-5 5-9a5 5 0 0 0-5-5z" fill="#2f6fb5"/><circle cx="7" cy="6" r="2" fill="#fff"/></svg>
      <span>42 Quayside Walk, Marlow<br>Harbour LH4 2QP</span>
    </div>
    <div class="abs contact" style="top:1320px">
      <svg width="16" height="16" viewBox="0 0 16 16"><path d="M3 1c1.5-.6 2 0 2.6 1.6l.5 1.3c.2.7-.7 1.2-1 1.6.8 1.8 2.1 3.1 3.9 4 .4-.4 1-1.3 1.7-1l1.3.6c1.6.6 2.2 1.3 1.5 2.7-1.4 2.2-4.2 1.8-7.2-.8C3 8.1 1.8 4.8 3 1z" fill="#2f6fb5"/></svg>
      <span>+ 44 (0) 20 5550 1842</span>
    </div>
    <div class="abs contact" style="top:1348px">
      <svg width="16" height="14" viewBox="0 0 16 14"><rect x="1" y="5" width="14" height="8" rx="1" fill="#2f6fb5"/><rect x="4" y="1" width="8" height="5" fill="none" stroke="#2f6fb5" stroke-width="1.5"/><rect x="4" y="8" width="8" height="2" fill="#fff"/></svg>
      <span>+ 44 (0) 20 5550 1907</span>
    </div>
    <div class="abs contact" style="top:1376px">
      <svg width="16" height="12" viewBox="0 0 16 12"><rect x="0" y="1" width="16" height="10" fill="#2f6fb5"/><path d="M0 1l8 6 8-6" fill="none" stroke="#fff" stroke-width="1.4"/></svg>
      <span>stay@restwellharbour.co.uk</span>
    </div>
  </footer>

</div>
</div>
</body>
</html>
```